Residential Mortgage Leader needs Wordpress Design

Looking for a home page website design for a client. We develop using the WordPress platform and would prefer the design be at least loosely based on an existing WordPress template. Attached files have many notes from our creative brief with client. The site must be responsive. Approved, basic wireframe attached. There is room for interpretation.

Existing web site: http://www.marisolkettering.example/

The Marisol Kettering Team relies on strong systems to deliver an on-time, done-right, friendly experience. Marisol offers mortgages and refinancing services throughout the United States. She is a successful Brookvale Funding agent who strives to be an active part of her community. She would like to focus the site on her team, rather than just her.

Difference makers...
When you work with the Marisol Kettering team you get a high level of expertise and a friendly experience.

She has amazing credentials. Marisol is widely recognized as a top producer for her company, and has earned a number of awards and honors for her customer service.

Marisol's team is very engaged and enjoys sharing social comments or photos from their community.

Imagery:
* Friendly, warm imagery, preferably of her team or an image to represent her team
* Clean and crisp
* Professional / Experts in mortgage and refinance
* Clean / Good use of white space
Updates

When possible, please use imagery from the DFW area. The client mentioned they would prefer not to see stock images. Thanks.

Amend that- creative use of stock images, however, is fine. A few designs have used stock imagery, but in a well-considered manner.

We added some photos and graphics that are local. We are Dallas / Ft. Worth, Plano, Frisco, Texas. We also added some examples of photos to use for the "In the Community" area. Stock photos of business folks just doesn't fit there. Thanks!

Target Market(s)

They service a lot of builders, but also work with homeowners. Their typical client is usually a woman searching for mortgage services online. She typically has a family and may refer her husband to Marisol's team. Keep in mind, however, they also see a number of other scenarios. Most of their clients are middle to high-end borrowers.

Industry/Entity Type

It Company

Requirements
Must have
• Design should be developed using program such as Photoshop or Fireworks or Illustrator as last preference. Ideally, the design would be based on an existing responsive WordPress theme, which we would customize. You must include the name of the target theme. The footer should include lots of space for disclaimers and legal language. Site navigation should include these choices: "Home, About, Builders, Mortgage Info, Approval, Blog, Contact"
Nice to have
• Blog, social media and photos area. Use of the already approved style prototype with colors and fonts (Lato- a Google font, Times New Roman and Cookie-a decorative Google font). However, we are open to interpretation.
Should not have
• Hard to read fonts or a lack of white space.

```html
<!DOCTYPE html>
<html lang="en">
<head>
<meta charset="utf-8">
<title>Brookvale Funding – Home</title>
<link href="https://fonts.googleapis.com/css2?family=Lato:wght@300;400;700&family=Cookie&family=Tinos&display=swap" rel="stylesheet">
<style>
:root{
  --red:#c1311d;
  --red-line:#c0392b;
  --blue:#1f88b8;
  --black:#0c0c0c;
  --nav-active:#5a5a5a;
  --page:#efefef;
  --card:#f6f6f6;
  --text:#555;
  --muted:#888;
  --footer:#2f2f2f;
  --footer-bottom:#262626;
  --footer-text:#cfcfcf;
  --white:#fff;
}
*{margin:0;padding:0;box-sizing:border-box}
html,body{width:907px;height:1200px;overflow:hidden}
body{position:relative;background:var(--page);font-family:Lato,Arial,sans-serif;color:var(--text)}
.abs{position:absolute}
.top-strip{left:0;top:0;width:907px;height:5px;background:var(--red)}
.header{left:0;top:5px;width:907px;height:89px;background:var(--white)}
.brand{left:82px;top:30px}
.brand-name{font-size:23px;font-weight:700;color:var(--red);letter-spacing:-.3px;display:flex;align-items:center;gap:8px}
.brand-name i{display:inline-block;width:14px;height:14px;background:var(--red)}
.brand-sub{font-size:11px;font-weight:700;color:#444;margin-top:2px}
.contact{left:682px;top:36px;display:flex;gap:8px;align-items:flex-start}
.contact-label{font-size:12px;color:#555;line-height:14px}
.contact-phone{font-size:13.5px;color:var(--red);line-height:16px}
.nav{left:0;top:94px;width:907px;height:38px;background:var(--black)}
.nav ul{list-style:none;position:absolute;left:83px;top:0;display:flex;height:38px}
.nav li{color:var(--white);font-size:12px;line-height:38px;padding:0 14px}
.nav li.active{background:var(--nav-active);padding:0 11px}
.nav li+li{margin-left:0}
.search{left:679px;top:102px;width:146px;height:22px;background:var(--white);border:1px solid #ccc;font-size:8px;color:#999;padding:5px 5px}
.hero{left:0;top:132px;width:825px;height:294px;background:var(--red)}
.hero-photo{left:0;top:132px}
.hero-title{left:90px;top:154px;font-family:Cookie,cursive;font-size:37px;color:var(--white)}
.hero-copy{left:90px;top:209px;width:285px;font-size:10px;line-height:13.6px;color:var(--white)}
.hero-copy p{margin-bottom:13.5px}
.btn{left:90px;top:362px;width:116px;height:33px;background:var(--white);border:1px solid #ddd;font-family:Tinos,"Times New Roman",serif;font-size:14px;color:#444;text-align:center;line-height:31px}
.tagline{left:90px;top:446px;width:727px;text-align:center;font-family:Tinos,"Times New Roman",serif;font-size:19px;line-height:25px;color:#555}
.card{background:var(--card)}
.card h2{font-family:Tinos,"Times New Roman",serif;font-weight:400;font-size:21px;color:var(--blue);padding:0 0 3px 8px;border-bottom:2px solid var(--red-line);height:30px;line-height:26px}
.card .body{padding:14px 8px 0 8px;font-size:9px;line-height:13.6px;color:#777;font-weight:300}
.card .body p{margin-bottom:13.5px}
.blog-item{display:flex;padding:12px 8px 0 6px;height:75px}
.date{width:30px;text-align:center;font-family:Tinos,"Times New Roman",serif;color:#444;border-right:1px solid #ddd;margin-right:8px;padding-right:2px;width:38px}
.date b{display:block;font-weight:400;font-size:28px;line-height:26px}
.date span{display:block;font-size:12px;line-height:15px}
.post h3{font-weight:400;font-size:13px;color:#555;line-height:15px;margin-bottom:3px}
.post p{font-size:9px;line-height:13.6px;color:#888;font-weight:300}
.post small{font-size:7.5px;color:#888}
.social{list-style:none;padding:10px 8px 0 8px;width:200px}
.social li{font-size:11.5px;color:#555;height:24px;line-height:22px;border-bottom:1px solid #e0e0e0}
.gallery{display:grid;grid-template-columns:92px 92px;gap:8px;padding:14px 0 0 9px}
.gallery div{height:63px}
.footer{left:0;top:938px;width:907px;height:224px;background:var(--footer)}
.footer-bottom{left:0;top:1162px;width:907px;height:38px;background:var(--footer-bottom)}
.portrait{left:95px;top:967px;width:110px;height:125px}
.agent{left:213px;top:966px;color:var(--footer-text);font-size:10px;line-height:17.4px}
.agent h4{font-weight:400;font-size:13.5px;line-height:17px;color:var(--white);margin-bottom:3px}
.agent .dir{margin-top:18px;color:var(--white)}
.fcol h5{font-weight:400;font-size:13.5px;color:var(--white);margin-bottom:14px;line-height:16px}
.fcol p,.fcol li{font-size:10px;line-height:17.4px;color:var(--footer-text);list-style:none}
.lang{left:637px;top:1110px;width:81px;height:24px;background:#3b3b3b;color:var(--footer-text);font-size:9.5px;line-height:24px;padding-left:7px}
.copy{left:96px;top:1173px;font-size:10px;color:var(--footer-text)}
.icons{left:702px;top:1169px;display:flex;gap:4px}
.icons span{width:20px;height:20px;display:block}
</style>
</head>
<body>
<div class="abs top-strip"></div>
<header class="abs header"></header>
<div class="abs brand">
  <div class="brand-name">Brookvale Funding <i></i></div>
  <div class="brand-sub">A Harborline Company</div>
</div>
<div class="abs contact">
  <svg width="28" height="30" viewBox="0 0 28 30" aria-hidden="true">
    <path d="M5 16 V12 A9 9 0 0 1 23 12 V16" fill="none" stroke="#333" stroke-width="2.2"/>
    <rect x="2" y="14" width="6" height="9" rx="2" fill="#333"/>
    <rect x="20" y="14" width="6" height="9" rx="2" fill="#333"/>
    <path d="M6 23 Q8 28 16 28" fill="none" stroke="#333" stroke-width="1.6"/>
  </svg>
  <div><div class="contact-label">Work With Us:</div><div class="contact-phone">0800-5550-142-6</div></div>
</div>
<nav class="abs nav">
  <ul>
    <li class="active">Home</li><li>About Us</li><li>Buliders</li><li>Mortgage Info</li><li>Blog</li><li>Contact Us</li>
  </ul>
</nav>
<div class="abs search">Enter your search...</div>

<section class="abs hero"></section>
<svg class="abs hero-photo" width="825" height="294" viewBox="0 0 825 294" role="img" aria-label="Family of four standing on a lawn in front of a red brick house under a blue sky">
  <defs>
    <linearGradient id="photoTone" x1="0" y1="0" x2="0" y2="1">
      <stop offset="0" stop-color="#6f9fd4"/>
      <stop offset=".45" stop-color="#a4574a"/>
      <stop offset=".8" stop-color="#8a5a48"/>
      <stop offset="1" stop-color="#6d8a2e"/>
    </linearGradient>
  </defs>
  <polygon points="540,0 825,0 825,294 248,294" fill="url(#photoTone)"/>
</svg>
<h1 class="abs hero-title">Earning Your Business</h1>
<div class="abs hero-copy">
  <p>Lorem ipsum dolor sit amet, consectetur adipisicing elit, sed do eiusmod tempor incididunt ut labore et dolore magna aliqua..</p>
  <p>Ut enim ad minim veniam, quis nostrud exercitation ullamco laboris nisi ut aliquip ex ea commodo consequat. Duis aute irure dolorpariatur.</p>
  <p>Excepteur sint occaecat cupidatat non proident, sunt culpa qui deserunt mollit anim id est laborum...</p>
</div>
<div class="abs btn">Get to Know Us</div>

<p class="abs tagline">Lorem ipsum dolor sit amet, consectetur adipisicing elit, sed do eiusmod tempor incididunt ut labore et dolore magna aliqua.</p>

<section class="abs card" style="left:90px;top:526px;width:280px;height:150px">
  <h2>Our Credentials</h2>
  <div class="body"><p>Lorem ipsum dolor sit amet, consectetur adipisicing exercitation ullamco elit, sed do eiusmod tempor veniam, quis nostrud exercitation ullamco incididunt ut labore et dolore magna aliqua.</p><p>Ut enim ad minim veniam, quis nostrud exercitation ullamco laboris nisi ut aliquip ex ea commodo consequat.</p></div>
</section>
<section class="abs card" style="left:382px;top:526px;width:212px;height:150px">
  <h2>Awards</h2>
  <div class="body"><p>Lorem ipsum dolor sit amet, consectetur adipisicing elit, sed do eiusmod tempor incididunt ut labore et dolore magna aliqua.</p><p>Ut enim ad minim veniam, quis nostrud exercitation ullamco laboris nisi ut aliquip....</p></div>
</section>
<section class="abs card" style="left:606px;top:526px;width:211px;height:150px">
  <h2>Recognion</h2>
  <div class="body"><p>Lorem ipsum dolor sit amet, consectetur adipisicing elit, sed do eiusmod tempor incididunt ut labore et dolore magna aliqua.</p><p>Ut enim ad minim veniam, quis nostrud exercitation ullamco laboris nisi ut aliquip....</p></div>
</section>

<section class="abs card" style="left:90px;top:712px;width:280px;height:194px">
  <h2>Blog</h2>
  <div class="blog-item">
    <div class="date"><b>2</b><span>Sep</span><span>2013</span></div>
    <div class="post"><h3>Bomowing</h3><p>Lorem ipsum dolor sit amet, consectetur adipisicing elit, sed do eiusmod tempor...</p><small>2 comments</small></div>
  </div>
  <div class="blog-item">
    <div class="date"><b>10</b><span>Sep</span><span>2013</span></div>
    <div class="post"><h3>Best Practices</h3><p>Lorem ipsum dolor sit amet, consectetur adipisicing elit, sed do eiusmod tempor...</p><small>2 comments</small></div>
  </div>
</section>
<section class="abs card" style="left:382px;top:712px;width:212px;height:194px">
  <h2>Social Media</h2>
  <ul class="social">
    <li>Subcribe Feeds</li><li>Our Circlebook Page</li><li>Follow Us On Chirpline</li><li>Snapfolio</li><li>Workweave</li>
  </ul>
</section>
<section class="abs card" style="left:606px;top:712px;width:211px;height:194px">
  <h2>In The Community</h2>
  <div class="gallery">
    <div role="img" aria-label="Team members standing together on a building porch" style="background:linear-gradient(#c9ccd0,#7d7470)"></div>
    <div role="img" aria-label="Large group of smiling community volunteers" style="background:linear-gradient(#e7d6b8,#c0783f)"></div>
    <div role="img" aria-label="Hands stacked together in a circle" style="background:linear-gradient(#e7b49a,#c97d62)"></div>
    <div role="img" aria-label="Group of colleagues posing outdoors" style="background:linear-gradient(#6d8fb0,#3c3f4a)"></div>
  </div>
</section>

<footer class="abs footer"></footer>
<div class="abs portrait" role="img" aria-label="Portrait of branch manager Marisol Kettering" style="background:linear-gradient(#6b4a3a,#3a2a24)"></div>
<div class="abs agent">
  <h4>Marisol Kettering<br>Branch Manager</h4>
  Office: 555.201.4410<br>Cell: 555.308.7721<br>mkettering@brookvalefunding.example<br>NMLS: 40219<br>2150 Cedar Plaza , Ste. 310<br>Alder Springs, TX 75990
  <div class="dir">Directions</div>
</div>
<div class="abs fcol" style="left:436px;top:966px">
  <h5>LINKS</h5>
  <ul><li>Home</li><li>About</li><li>Builders</li><li>Mortgage Info</li><li>Approval</li><li>Blog</li><li>Contact Us</li></ul>
</div>
<div class="abs fcol" style="left:636px;top:966px">
  <h5>ADDRESS</h5>
  <p>Our Address<br>Corporate Office - 4400 Lindenwood Avenue,<br>Suite 700 Dallas, Texas 75390</p>
  <p style="margin-top:17px">Tel : 1-800-555-0199<br>Email : Contact Brookvale Funding</p>
</div>
<div class="abs lang">Language... <svg width="8" height="6" viewBox="0 0 8 6" style="margin-left:6px"><path d="M1 1 L4 4 L7 1" fill="none" stroke="#cfcfcf" stroke-width="1.2"/></svg></div>
<div class="abs footer-bottom"></div>
<p class="abs copy">Copyright © 2013 Brookvale Funding. All Rights Reserved</p>
<div class="abs icons">
  <span style="background:#5aaed6"></span><span style="background:#3b5a9a"></span><span style="background:#e0662a"></span><span style="background:#555"></span>
</div>
</body>
</html>
```